Wellness bold & beautiful PowerPoint Template

I will like a PowerPoint template, matching my brand, designed for my business.
- Some words that describe our brand identity are: wellness, natural, calming, simplicity, clean
- For icons, we prefer line icons.
- Website: http://www.vendrabo.com/
- PowerPoint board: https://www.pinterest.com/morelistavy/vendrabo-powerpoint/
- Branding board: https://www.pinterest.com/morelistavy/vendrabo-branding/
FYI: I am attaching a rough draft of a powerpoint presentation we are preparing
Target Market(s)
Women 23-48 interested in wellness
Industry/Entity Type
Health And Wellness
Font styles to use
Other font styles liked:
- Open Sans, Helvitica, Meddon
Requirements
Must have
- cover page, about page, author page, table of content, table format, graph format, list format, 2 column template.
Nice to have
- time line page sample

```html
<!DOCTYPE html>
<html lang="en">
<head>
<meta charset="utf-8">
<title>Our Team</title>
<link href="https://fonts.googleapis.com/css2?family=Open+Sans:wght@400;700&display=swap" rel="stylesheet">
<style>
  :root {
    --leaf-dark: #0a2a12;
    --leaf-mid: #1f6b34;
    --leaf-light: #46b062;
    --card: #ffffff;
    --frame-green: #5f9a3a;
    --ink-heading: #2e2d45;
    --ink-body: #222222;
    --magenta: #b1228a;
    --green: #66993c;
    --blue: #2ea7da;
    --white: #ffffff;
  }
  * { margin: 0; padding: 0; box-sizing: border-box; }
  html, body { width: 1200px; height: 675px; overflow: hidden; }
  body { font-family: "Open Sans", Helvetica, Arial, sans-serif; }

  .slide {
    position: relative;
    width: 1200px;
    height: 675px;
    overflow: hidden;
  }
  .foliage-backdrop {
    position: absolute;
    inset: 0;
    background:
      radial-gradient(circle at 20% 30%, var(--leaf-light) 0, transparent 35%),
      radial-gradient(circle at 85% 70%, var(--leaf-light) 0, transparent 35%),
      radial-gradient(circle at 60% 95%, var(--leaf-mid) 0, transparent 40%),
      linear-gradient(135deg, var(--leaf-mid), var(--leaf-dark) 55%, var(--leaf-mid));
  }
  .card {
    position: absolute;
    left: 78px; top: 44px;
    width: 1044px; height: 586px;
    background: var(--card);
  }
  .card-frame {
    position: absolute;
    left: 22px; top: 22px;
    width: 1000px; height: 543px;
    border: 3px solid var(--frame-green);
  }
  .slide-title {
    position: absolute;
    left: 43px; top: 30px;
    font-size: 32px;
    font-weight: 700;
    letter-spacing: 0.5px;
    color: var(--ink-heading);
    line-height: 1;
  }
  .member {
    position: absolute;
    top: 99px;
    width: 296px;
  }
  .member--one { left: 48px; }
  .member--two { left: 374px; }
  .member--three { left: 702px; }

  .member-portrait {
    display: block;
    width: 236px; height: 236px;
    margin: 0 0 0 24px;
  }
  .member-name {
    width: 192px;
    height: 36px;
    margin: 20px 0 0 51px;
    color: var(--white);
    font-size: 19px;
    font-weight: 700;
    line-height: 36px;
    text-align: center;
  }
  .member--one .member-name { background: var(--magenta); }
  .member--two .member-name { background: var(--green); }
  .member--three .member-name { background: var(--blue); }

  .member-bio {
    margin-top: 25px;
    font-size: 15px;
    line-height: 27px;
    color: var(--ink-body);
    text-align: justify;
  }
</style>
</head>
<body>
<div class="slide">
  <div class="foliage-backdrop" role="img" aria-label="Background of dense green leaves"></div>
  <div class="card">
    <div class="card-frame"></div>
    <h1 class="slide-title">OUR TEAM</h1>

    <div class="member member--one">
      <svg class="member-portrait" viewBox="0 0 236 236" role="img" aria-label="Team member photo placeholder">
        <circle cx="118" cy="118" r="118" fill="var(--magenta)"/>
        <rect x="66" y="66" width="104" height="104" rx="4" fill="none" stroke="var(--white)" stroke-width="8"/>
      </svg>
      <div class="member-name">NAME #1</div>
      <p class="member-bio">Lorem ipsum dolor sit amet, consectetur adipiscing elit. Aliquam tincidunt ante nec sem congue convallis. Pellentesque vel mauris quis nisl ornare rutrum in id risus. Proin vehicula ut</p>
    </div>

    <div class="member member--two">
      <svg class="member-portrait" viewBox="0 0 236 236" role="img" aria-label="Team member photo placeholder">
        <circle cx="118" cy="118" r="118" fill="var(--green)"/>
        <rect x="66" y="66" width="104" height="104" rx="4" fill="none" stroke="var(--white)" stroke-width="8"/>
      </svg>
      <div class="member-name">NAME #2</div>
      <p class="member-bio">Lorem ipsum dolor sit amet, consectetur adipiscing elit. Aliquam tincidunt ante nec sem congue convallis. Pellentesque vel mauris quis nisl ornare rutrum in id risus. Proin vehicula ut</p>
    </div>

    <div class="member member--three">
      <svg class="member-portrait" viewBox="0 0 236 236" role="img" aria-label="Team member photo placeholder">
        <circle cx="118" cy="118" r="118" fill="var(--blue)"/>
        <rect x="66" y="66" width="104" height="104" rx="4" fill="none" stroke="var(--white)" stroke-width="8"/>
      </svg>
      <div class="member-name">NAME #3</div>
      <p class="member-bio">Lorem ipsum dolor sit amet, consectetur adipiscing elit. Aliquam tincidunt ante nec sem congue convallis. Pellentesque vel mauris quis nisl ornare rutrum in id risus. Proin vehicula ut</p>
    </div>
  </div>
</div>
</body>
</html>
```